Bramblewood Card Company Business Cards

We are a trading card store with Glimmorax, sports and other TCG cards, we need a business card design that encompasses a clean cut, modern style with a retro flare. website is bramblewoodcardco.com for reference. Can utilize a comic book era feel or a more modern outdoor feel to utilize the "Pacific Northwest" elements of tress, mountains, etc.

Industry/Entity Type

Trading cards and collectibles

Contact Information for Business Card

business name, email address, phone number, name, owner job title

Font styles to use
Sans Serif

```html
<!DOCTYPE html>
<html lang="en">
<head>
<meta charset="utf-8">
<title>Bramblewood Card Company – Business Cards</title>
<link rel="stylesheet" href="https://fonts.googleapis.com/css2?family=Montserrat:wght@400;500;700&display=swap">
<style>
  :root {
    --page: #e9e6e1;
    --card-white: #ffffff;
    --card-black: #000000;
    --accent: #16b8dc;
    --logo-grey: #7a7a7a;
    --ink: #1b1b1b;
  }
  * { box-sizing: border-box; margin: 0; padding: 0; }
  html, body { width: 1200px; height: 931px; overflow: hidden; }
  body {
    background: var(--page);
    font-family: "Montserrat", sans-serif;
    position: relative;
  }
  .card {
    position: absolute;
    width: 620px;
    height: 354px;
    border-radius: 22px;
    overflow: hidden;
    box-shadow: 0 10px 28px rgba(0,0,0,.28);
  }
  .card::after {
    content: "";
    position: absolute;
    left: 0; right: 0; bottom: 0;
    height: 14px;
    background: var(--accent);
  }
  .card-back { left: 60px; top: 70px; background: var(--card-black); }
  .card-front { left: 520px; top: 470px; background: var(--card-white); }

  .brand {
    position: absolute;
    display: flex;
    align-items: center;
    gap: 12px;
    color: var(--logo-grey);
    font-weight: 700;
    text-transform: uppercase;
    letter-spacing: .04em;
    line-height: 1.15;
  }
  .brand-dot {
    flex: none;
    border-radius: 50%;
    background: var(--logo-grey);
  }
  .card-back .brand { left: 50%; top: 50%; transform: translate(-50%, -56%); font-size: 28px; }
  .card-back .brand-dot { width: 40px; height: 40px; }
  .card-front .brand { right: 40px; top: 48px; font-size: 21px; text-align: left; }
  .card-front .brand-dot { width: 32px; height: 32px; }

  .person { position: absolute; left: 46px; top: 178px; }
  .person-name { color: var(--accent); font-weight: 700; font-size: 31px; line-height: 1; }
  .person-title { color: var(--ink); font-size: 15px; margin-top: 4px; }
  .divider {
    position: absolute;
    left: 46px; right: 40px; top: 236px;
    height: 1.5px;
    background: var(--accent);
  }
  .contacts {
    position: absolute;
    left: 46px; top: 250px;
    list-style: none;
    font-size: 14px;
    color: var(--ink);
    line-height: 24px;
  }
  .contacts li { display: flex; align-items: center; gap: 10px; }
  .contacts svg { width: 15px; height: 15px; fill: var(--accent); flex: none; }
  .address {
    position: absolute;
    right: 40px; top: 258px;
    font-size: 14px;
    color: var(--ink);
    text-align: right;
    line-height: 20px;
  }
</style>
</head>
<body>
  <section class="card card-back" aria-label="Card back">
    <div class="brand"><span class="brand-dot"></span><span>Bramblewood<br>Card Company</span></div>
  </section>

  <section class="card card-front" aria-label="Card front">
    <div class="brand"><span class="brand-dot"></span><span>Bramblewood<br>Card Company</span></div>

    <div class="person">
      <p class="person-name">Darren Holt</p>
      <p class="person-title">Owner</p>
    </div>
    <div class="divider"></div>

    <ul class="contacts">
      <li>
        <svg viewBox="0 0 24 24" aria-hidden="true"><path d="M6.6 10.8a15.1 15.1 0 0 0 6.6 6.6l2.2-2.2a1 1 0 0 1 1-.25 11.4 11.4 0 0 0 3.6.57 1 1 0 0 1 1 1V20a1 1 0 0 1-1 1A17 17 0 0 1 3 4a1 1 0 0 1 1-1h3.5a1 1 0 0 1 1 1c0 1.25.2 2.45.57 3.57a1 1 0 0 1-.25 1z"/></svg>
        06-48215370
      </li>
      <li>
        <svg viewBox="0 0 24 24" aria-hidden="true"><path d="M2 5h20v14H2z M2 5l10 8 10-8" /></svg>
        info@bramblewoodcardco.com
      </li>
      <li>
        <svg viewBox="0 0 24 24" aria-hidden="true"><circle cx="12" cy="12" r="10"/></svg>
        www.bramblewoodcardco.com
      </li>
    </ul>

    <p class="address">4710 Alder Hollow Ave Suite 118<br>Portland, Oregon 97205</p>
  </section>
</body>
</html>
```